Business Cards for IT Consulting Company (Managed Service Provider)

I am looking to have some business cards printed and would like some designs. We are an IT Consulting company based in Vancouver BC. I would like a nice clean and modern look to the cards. I have uploaded all the versions of my logo so parts can be used as needed. Here is a snippit from our website homepage:

Quillbrook Networks Ltd. is an IT Solutions Partner located in Vancouver BC, Canada. We offer IT solutions and support to customers in the greater Vancouver Area. With expertise in Microsoft platforms, as well as Linux and Mac OSX and over 12 years experience in the IT industry, Quillbrook Networks is dedicated to offering our clients top quality service and products. We take pride in the solutions we offer our customers. The greatest compliment a client can give us is to recommend our services.

Quillbrook Networks Ltd. offers a wide range of IT services from onsite service to remote support and managed service solutions. This allows clients to choose the support path that best suits their company’s needs. Supporting many different sized companies from small to enterprise level over the past 12 years Quillbrook Networks has the experience and expertise needed to ensure things run smoothly. Allowing our clients to focus on doing business.

Revolutionizing the way IT services are delivered.

Quillbrook Networks is dedicated to providing our clients with IT solutions that work and grow with them for years to come. This philosophy helps save money in the long run instead of replacing equipment constantly. Far too often IT solutions are not well thought out and while possibly solving the problem at hand, require replacement due to growth or quality within a very short time frame. Quillbrook Networks takes pride in providing solutions that will last and be able to accommodate growth without the need for replacement.

Industry/Entity Type

Information Technology

Contact Information for Business Card

Quillbrook Networks Ltd.
(Employee Name)
Eml: (Employees Email Address)
Web: quillbrook.me
Ph: 604-555-0148

Font styles to use
Serif
Sans Serif

Requirements
Must have
• The Company logo and company colors.
Nice to have
• - Our tag line: "Revolutionizing IT Services" or "Revolutionizing the way IT services are delivered."
• - Also I really like the idea of nature and technology together blending which is sort of where my logo came from so integrating that somehow onto the business cards would be great.

```html
<!DOCTYPE html>
<html lang="en">
<head>
<meta charset="utf-8">
<title>Quillbrook Networks Ltd. — Business Cards</title>
<link rel="stylesheet" href="https://fonts.googleapis.com/css2?family=Montserrat:wght@500;600&family=Roboto:ital,wght@0,400;1,400&display=swap">
<style>
  :root {
    --backdrop: #a9a7a7;
    --card: #1e1f21;
    --card-deep: #1b1c1e;
    --pattern-tone: #232426;
    --brand-blue: #1b8fd6;
    --band-grey: #5b5b5d;
    --text-light: #e6e6e6;
    --text-muted: #bdbdbd;
    --divider: #9a9a9a;
  }
  * { margin: 0; padding: 0; box-sizing: border-box; }
  html, body { width: 1200px; height: 1200px; overflow: hidden; }
  body { background: var(--backdrop); position: relative; font-family: "Montserrat", sans-serif; }

  .card { position: absolute; width: 713px; height: 420px; background: var(--card); overflow: hidden; }
  .card--front { left: 238px; top: 117px; }
  .card--back { left: 231px; top: 642px; height: 419px; }

  /* front */
  .front-texture { position: absolute; inset: 0; background: var(--card-deep); }
  .front-wordmark {
    position: absolute; left: 0; right: 0; top: 150px; text-align: center;
    color: var(--brand-blue); font-weight: 600; line-height: 1;
  }
  .front-wordmark .name-main { display: block; font-size: 66px; letter-spacing: 0.5px; }
  .front-wordmark .name-sub { display: block; font-size: 24px; letter-spacing: 1.5px; margin-top: 10px; }
  .front-tagline {
    position: absolute; left: 0; right: 0; top: 377px; display: flex;
    justify-content: center; align-items: center; gap: 16px;
    color: var(--text-light); font-size: 18px; font-weight: 500;
  }
  .front-tagline .rule { width: 110px; height: 3px; background: var(--brand-blue); }

  /* back */
  .back-decoration {
    position: absolute; left: 284px; top: 18px; width: 396px; height: 340px;
    background: radial-gradient(ellipse at center, var(--pattern-tone) 0%, var(--card) 72%);
  }
  .back-wordmark {
    position: absolute; left: 40px; width: 260px; top: 176px; text-align: center;
    color: var(--brand-blue); font-weight: 600; font-size: 24px; line-height: 1.2;
  }
  .back-divider { position: absolute; left: 329px; top: 78px; width: 2px; height: 254px; background: var(--divider); }
  .contact { position: absolute; left: 389px; top: 124px; font-family: "Roboto", sans-serif; }
  .contact-name { font-family: "Montserrat", sans-serif; color: var(--brand-blue); font-size: 25px; font-weight: 600; }
  .contact-role { color: var(--text-muted); font-size: 16px; font-style: italic; margin-top: 6px; }
  .contact-list { list-style: none; margin-top: 22px; }
  .contact-list li { display: flex; align-items: center; gap: 17px; color: var(--text-light); font-size: 18px; height: 27.5px; }
  .contact-list svg { width: 18px; height: 18px; fill: var(--brand-blue); }

  .base-band { position: absolute; left: 0; bottom: 0; width: 100%; height: 28px; background: var(--band-grey); }
  .tagline-tab {
    position: absolute; right: 0; bottom: 0; width: 400px; height: 53px; background: var(--brand-blue);
    clip-path: polygon(30px 0, 100% 0, 100% 100%, 0 100%);
    display: flex; align-items: center; justify-content: center; padding-left: 12px;
    color: #fff; font-size: 19px; font-weight: 500;
  }
</style>
</head>
<body>

<section class="card card--front">
  <div class="front-texture" role="img" aria-label="Subtle dark repeating geometric background pattern"></div>
  <h1 class="front-wordmark"><span class="name-main">Quillbrook</span><span class="name-sub">NETWORKS LTD.</span></h1>
  <p class="front-tagline"><span class="rule"></span>Revolutionizing IT Services<span class="rule"></span></p>
</section>

<section class="card card--back">
  <div class="back-decoration" role="img" aria-label="Faint large geometric decoration behind the contact details"></div>
  <p class="back-wordmark">Quillbrook Networks</p>
  <div class="back-divider"></div>
  <div class="contact">
    <p class="contact-name">Daniel Moreau</p>
    <p class="contact-role">Managing Director</p>
    <ul class="contact-list">
      <li>
        <svg viewBox="0 0 24 24" aria-hidden="true"><path d="M3 7c0-2 3-3 9-3s9 1 9 3v2h-5V7.5c-1-.4-2.5-.5-4-.5s-3 .1-4 .5V9H3V7zm4 3h10l2 9H5l2-9zm5 2a3 3 0 100 6 3 3 0 000-6z"/></svg>
        604-555-0148
      </li>
      <li>
        <svg viewBox="0 0 24 24" aria-hidden="true"><path d="M12 2a10 10 0 100 20 10 10 0 000-20zm6.9 9h-3a15 15 0 00-1.2-5.6A8 8 0 0118.9 11zM12 4c.9 1.2 1.8 3.6 1.9 7h-3.8c.1-3.4 1-5.8 1.9-7zM9.3 5.4A15 15 0 008.1 11h-3a8 8 0 014.2-5.6zM5.1 13h3a15 15 0 001.2 5.6A8 8 0 015.1 13zm6.9 7c-.9-1.2-1.8-3.6-1.9-7h3.8c-.1 3.4-1 5.8-1.9 7zm2.7-1.4a15 15 0 001.2-5.6h3a8 8 0 01-4.2 5.6z"/></svg>
        www.quillbrook.me
      </li>
      <li>
        <svg viewBox="0 0 24 24" aria-hidden="true"><path d="M2 5h20v14H2V5zm2 2v.5l8 5.5 8-5.5V7H4zm0 3v7h16v-7l-8 5.5L4 10z"/></svg>
        support@quillbrook.me
      </li>
    </ul>
  </div>
  <div class="base-band"></div>
  <p class="tagline-tab">Revolutionizing IT Services</p>
</section>

</body>
</html>
```